Valmora Company needs a Business Card Design

We just opened our business recently and we need a business card design. Our basic product are clothes and accessories. We would like to see designs that use bright colors like pink, light blue and purple. In addition to that kindly include also our address in the business card which our main office is located in Los Angeles, California.
The final design should communicate that we have affordable price yet high quality brand.

Target Market(s)

young and middle age women

Industry/Entity Type

Business

Contact Information for Business Card

Valmora Apparel and Accessories 4873 North Bellcrest St. Los Angeles California
Tel: 555-318-6492

Logo Text

Valmora's Apparel and Accessories

Font styles to use
Serif

Requirements
Must have
• there should be a graphic of a sexy lady wearing an elegant dress at the upper left corner of the business card.

```html
<!DOCTYPE html>
<html lang="en">
<head>
<meta charset="utf-8">
<title>Valmora Apparel and Accessories – Business Card</title>
<link rel="stylesheet" href="https://fonts.googleapis.com/css2?family=Arimo:wght@400&display=swap">
<style>
  :root {
    --page-bg: #e9e7e4;
    --card-white: #ffffff;
    --card-white-soft: #f1f1f1;
    --band-light: #d6d6d6;
    --band-dark: #a9a9a9;
    --brand-pink: #d640b4;
    --text-grey: #555555;
    --figure-dark: #1c1c1c;
    --figure-mid: #6a6a6a;
  }
  * { margin: 0; padding: 0; box-sizing: border-box; }
  html, body {
    width: 1200px;
    height: 818px;
    overflow: hidden;
    background: var(--page-bg);
    font-family: "Arimo", Arial, sans-serif;
  }
  .card {
    position: absolute;
    left: 100px;
    top: 123px;
    width: 1000px;
    height: 572px;
    background: linear-gradient(180deg, var(--card-white) 0%, var(--card-white-soft) 100%);
    box-shadow: 0 6px 22px rgba(0,0,0,0.18);
    overflow: hidden;
  }
  .card__band {
    position: absolute;
    left: 0;
    top: 268px;
    width: 100%;
    height: 304px;
    background: linear-gradient(180deg, var(--band-light) 0%, var(--band-dark) 100%);
  }
  .card__figure {
    position: absolute;
    left: 60px;
    top: 120px;
    width: 230px;
    height: 420px;
    border-radius: 110px 110px 14px 14px;
    background: linear-gradient(180deg, var(--figure-dark) 0%, var(--figure-dark) 40%, var(--figure-mid) 100%);
  }
  .brand {
    position: absolute;
    left: 330px;
    top: 62px;
  }
  .brand__name {
    font-size: 128px;
    line-height: 1;
    color: var(--brand-pink);
    letter-spacing: 1px;
  }
  .brand__tagline {
    margin-top: 8px;
    font-size: 36px;
    color: var(--text-grey);
  }
  .contact {
    position: absolute;
    left: 360px;
    top: 330px;
    color: var(--text-grey);
  }
  .contact__phone {
    font-size: 46px;
    letter-spacing: 1px;
  }
  .contact__address {
    margin-top: 40px;
    font-size: 27px;
  }
</style>
</head>
<body>
  <main class="card">
    <div class="card__band"></div>
    <div class="card__figure" role="img" aria-label="Silhouette of a woman in an elegant evening gown"></div>
    <header class="brand">
      <h1 class="brand__name">Valmora</h1>
      <p class="brand__tagline">Apparel and Accessories</p>
    </header>
    <section class="contact">
      <p class="contact__phone">Tel: 555-318-6492</p>
      <p class="contact__address">4873 North Bellcrest St. Los Angeles California</p>
    </section>
  </main>
</body>
</html>
```